Personal Business card and maybe logo or graphic?

I would like a card to give out like you would a business card, however I am not promoting a business, it is just for my personal details.

I have no brand and no logo to worry about.

I would like some images or a logo of some kind or a graphic so the card has some excitement about it.

I am happy if you wish to create a logo/graphic that represents my name, I have seen someone with just their initials as a graphic so for me PH, however I am happy for you to create anything you wish, it does not have to relate to me just make the card look fun and still professional.

Please use the details

Peter Hollis

Ashcombe House
9 The Croft
Elm Rise
Bournemouth
Dorset
BH4 2QP

+44 (0)7812 604258
peter@hollispost.com
linkedin.com/in/hollispeter

looking for a mix between fun, fresh , young whilst being professional

I am new to this and am looking for you to guide me through the process please ask questions and ideas

I am just tidying up my brief as I am starting to understand more. hope it has not confused anyone
Updates

Reason: I have not had time to review or comment due to personal issues sorry

Hi,

to help would you be so kind as to use these sample details on the card

I am uk based and a few designs have us details which look different

Peter Hollis

Ashcombe house

9 The Croft

Elm Rise

Bournemouth

Dorset

BH4 2QP

+44 (0)7812 604258

peter@hollispost.com

many thanks hope that is ok and not too much trouble!

regards

Pete

My are of expertise is IT management / IT Consultancy, incase you wish to incorporate any graphics

My job was that of CIO (Chief Information Officer) or another term is Head of IT

just advising incase this gives any assistance as one designer has asked s may be useful to others

thanks                                   

just thought I have had a look and the UK size for a business card seems to be as per below

I thought I would mention as I guess the US size may be different and other countries too

I found these sizes on Cardforge but guess most companies will be similar

that said maybe you can advise me

I have no idea what cardforge is like so not sure where to get cards made, will figure that out later I guess but I assume dimensions are important for the design

thanks

 

Document Trim Size    

            Horizontal        

        85 x 55 mm           

1004 x 650 pixels           

            Vertical        

        55 x 85 mm           

650 x 1004 pixels           

        Full Bleed Size    

            Horizontal        

        88 x 58 mm           

1039 x 685 pixels           

            Vertical        

        58 x 88 mm           

685 x 1039 pixels           

 many thanks

Target Market(s)

Professional and personal contacts

Industry/Entity Type

Business

```html
<!DOCTYPE html>
<html lang="en">
<head>
<meta charset="utf-8">
<title>Personal Business Card</title>
<link href="https://fonts.googleapis.com/css2?family=Montserrat:wght@400;500;700&display=swap" rel="stylesheet">
<style>
  :root {
    --canvas-bg: #d9d9d9;
    --card-front: #000000;
    --card-back-start: #f7f3ee;
    --card-back-end: #efe6f3;
    --ink: #111111;
    --ink-soft: #2a2a2a;
    --script-yellow: #f5d36a;
    --script-peach: #d9907f;
    --script-pink: #c47aa6;
    --script-purple: #9b4fb0;
    --script-red: #9e2a2a;
    --accent-dot: #9a45b0;
    --icon-mail: #4fae3c;
    --icon-social: #1a72c0;
    --shadow: 0 12px 28px rgba(0,0,0,0.18);
  }
  * { box-sizing: border-box; margin: 0; padding: 0; }
  html, body {
    width: 1200px; height: 900px; overflow: hidden;
    background: var(--canvas-bg);
    font-family: "Montserrat", sans-serif;
  }
  .canvas {
    width: 1200px; height: 900px;
    display: flex; align-items: center; justify-content: center; gap: 60px;
  }
  .card {
    position: relative;
    width: 520px; height: 336px;
    border-radius: 4px;
    box-shadow: var(--shadow);
    overflow: hidden;
  }
  .card--front { background: var(--card-front); }
  .monogram {
    position: absolute;
    left: 16%; top: 28%;
    width: 70%; height: 30%;
    border-radius: 60px;
    background: linear-gradient(90deg, var(--script-yellow) 0%, var(--script-peach) 25%, var(--script-pink) 50%, var(--script-purple) 78%, var(--script-red) 100%);
    opacity: 0.9;
  }
  .monogram-dot {
    position: absolute;
    left: 58.5%; top: 74%;
    width: 20px; height: 20px;
    border-radius: 50%;
    background: var(--accent-dot);
  }
  .card--back {
    background: linear-gradient(120deg, var(--card-back-start) 0%, var(--card-back-end) 100%);
    color: var(--ink);
  }
  .back-flourish {
    position: absolute;
    left: 30%; top: 6%;
    width: 66%; height: 78%;
    border-radius: 120px;
    background: linear-gradient(120deg, rgba(230,214,214,0.35), rgba(214,190,226,0.45));
  }
  .identity {
    position: absolute;
    left: 40px; top: 44px;
  }
  .identity__name {
    font-size: 22px; font-weight: 700; letter-spacing: 0.2px;
    margin-bottom: 6px;
  }
  .identity__address {
    font-style: normal;
    font-size: 14px; line-height: 1.2; font-weight: 400;
    color: var(--ink-soft);
  }
  .identity__web {
    margin-top: 12px;
    font-size: 12px; font-weight: 500;
  }
  .contact {
    position: absolute;
    right: 36px; bottom: 44px;
    text-align: right;
  }
  .contact__phone {
    font-size: 19px; font-weight: 700; letter-spacing: 0.5px;
    margin-bottom: 4px;
  }
  .contact__line {
    display: flex; align-items: center; justify-content: flex-end; gap: 8px;
    font-size: 12.5px; font-weight: 500; line-height: 1.5;
  }
  .contact__icon {
    width: 14px; height: 14px; border-radius: 50%; flex: none;
  }
  .contact__icon--mail { background: var(--icon-mail); }
  .contact__icon--social { background: var(--icon-social); }
</style>
</head>
<body>
  <main class="canvas">
    <section class="card card--front" aria-label="Card front">
      <div class="monogram" role="img" aria-label="Flowing script monogram in a yellow to purple to red gradient"></div>
      <div class="monogram-dot"></div>
    </section>

    <section class="card card--back" aria-label="Card back">
      <div class="back-flourish" role="img" aria-label="Faint script monogram watermark in soft pink and lilac"></div>
      <div class="identity">
        <h1 class="identity__name">Your Full Name</h1>
        <address class="identity__address">
          234 Lorem ipsum<br>
          Dolor sit amet<br>
          12345 MSD2321<br>
          COUNTRY
        </address>
        <p class="identity__web">www.yourweblink.com</p>
      </div>
      <div class="contact">
        <p class="contact__phone">+11 01234567</p>
        <p class="contact__line">abc@mailhaven.com <span class="contact__icon contact__icon--mail"></span></p>
        <p class="contact__line">www.netprofile.com/URLinformation <span class="contact__icon contact__icon--social"></span></p>
      </div>
    </section>
  </main>
</body>
</html>
```